Website for a Psychologist in Private Practice

I need a cool web design for my website: www.drkalvoric.com. I would like it to look professional. Keep all the current content and add: Space for video; radio spots (see Silver Cedar Tunes Logo below for those); Quick Inquiry; Friendora link; 5 star rating on Rivo; a map; reviews from former patients. I am open to suggestions.

Target Market(s)

Those seeking individual and marital counseling.

Industry/Entity Type

Mental Health

Number of Pages Required

1 page

Font styles to use
Sans Serif
Other font styles liked:
• I'm open but no hard to read script

Requirements
Must have
• All the content on my home page with link for video and radio spots. List services and degrees and expertices (pics not necessary).
Nice to have
• A video of me and radio conversations (logo of Silver Cedar Tunes radio attached).
Should not have
• Cartoons, comedy, etc.... I don't need pictures of services (marital, depression, etc...) Just list those.

```html
<!DOCTYPE html>
<html lang="en">
<head>
<meta charset="utf-8">
<title>Dr. Mara L. Kalvoric – Individual and Marital Counseling</title>
<link rel="stylesheet" href="https://fonts.googleapis.com/css2?family=Lato:wght@400;700;900&family=Raleway:wght@600&family=Allura&display=swap">
<style>
:root{
  --blue:#2a84c4;
  --blue-dark:#1f6fa8;
  --gold:#c9ad5a;
  --gold-soft:#d9c47f;
  --nav:#333333;
  --ink:#2b2b2b;
  --text:#444444;
  --muted:#777777;
  --line:#dddddd;
  --paper:#ffffff;
  --card:#e4e4e4;
  --band:#f4f4f4;
  --footer:#2e2e2e;
}
*{box-sizing:border-box;margin:0;padding:0}
html,body{width:1200px;height:2667px;overflow:hidden}
body{font-family:"Lato",Arial,sans-serif;color:var(--text);background:var(--paper);position:relative}
.script{font-family:"Allura",cursive;font-weight:400}

/* header */
.site-header{height:114px;background:#fafafa;display:flex;align-items:center;padding:0 80px;justify-content:space-between}
.brand{font-family:"Allura",cursive;font-size:50px;color:var(--gold);line-height:1}
.contact-pills{display:flex;gap:12px}
.pill{height:42px;border:1px solid var(--line);border-radius:21px;background:#fff;display:flex;align-items:center;gap:12px;padding:0 26px;font-size:16px;color:var(--ink)}
.pill svg{width:18px;height:18px}
.pill b{font-weight:700}

/* nav */
.main-nav{height:64px;background:var(--nav);display:flex;align-items:center;justify-content:space-between;padding:0 80px 0 80px}
.main-nav a{color:#fff;text-decoration:none;font-weight:700;font-size:19px;letter-spacing:.2px;padding:9px 10px}
.main-nav a.active{background:var(--blue)}

/* hero */
.hero{position:relative;height:483px;background:linear-gradient(90deg,#8b8780 0%,#d9d9d6 25%,#eef0f2 45%,#b9cde2 70%,#e7e8ea 100%)}
.hero-arrow{position:absolute;top:188px;width:30px;height:30px;background:#333;display:flex;align-items:center;justify-content:center}
.hero-arrow.left{left:10px}.hero-arrow.right{right:10px}
.hero-caption{position:absolute;left:0;right:0;bottom:0;height:74px;background:rgba(40,40,40,.55);color:#fff;font-family:"Raleway",sans-serif;font-weight:600;font-size:29px;display:flex;align-items:center;justify-content:center}

/* about */
.about{height:491px;position:relative}
.about-body{position:absolute;left:80px;top:80px;width:685px}
.section-title{font-size:56px;color:var(--ink);line-height:1}
.section-title .accent{color:var(--gold)}
.about .section-title{font-size:48px}
.underline{width:105px;height:3px;background:var(--blue);margin-top:4px}
.about p{font-size:14.5px;line-height:26px;color:var(--ink);margin-top:24px}
.about p b{font-weight:700}
.values{display:flex;gap:40px;margin-top:30px}
.value{display:flex;gap:14px;width:330px}
.value-icon{width:78px;height:78px;border:2px solid var(--blue);border-radius:50%;flex:none;display:flex;align-items:center;justify-content:center}
.value h3{color:var(--blue);font-weight:400;font-size:21px;margin-top:6px}
.value h3 + p{margin-top:8px;font-size:14.5px;line-height:20px}

.inquiry{position:absolute;left:807px;top:82px;width:313px;height:332px;background:#ececec;border-radius:5px}
.inquiry h2{height:48px;background:var(--blue);color:#fff;font-size:20px;font-weight:700;display:flex;align-items:center;padding-left:24px;border-radius:5px 5px 0 0;margin:0 -2px}
.inquiry form{padding:10px 24px 0}
.field{height:35px;background:#fff;border:1px solid #d2d2d2;font-size:13px;color:#555;display:flex;align-items:center;padding-left:10px;margin-bottom:7px;position:relative}
.field.select::after{content:"";position:absolute;right:12px;top:14px;border:6px solid transparent;border-top-color:var(--gold)}
.field.area{height:68px;align-items:flex-start;padding-top:10px}
.submit{display:inline-flex;width:96px;height:40px;background:var(--blue);color:#fff;font-weight:700;font-size:16px;align-items:center;justify-content:center;margin-top:6px}

/* sessions + video */
.feature-band{height:355px;display:flex}
.sessions{width:600px;background:linear-gradient(135deg,#d2ba6c,#c7ad5e 60%,#bfa35a);color:#fff;text-align:center;padding-top:24px}
.sessions h2{font-size:36px;font-weight:700;margin-top:10px}
.session-list{display:grid;grid-template-columns:160px 180px;column-gap:0;row-gap:11px;justify-content:center;text-align:left;margin-top:14px;font-size:14px;color:var(--ink)}
.session-list li{list-style:none;display:flex;align-items:center;gap:8px}
.session-list li.strong{font-weight:700}
.btn-outline{display:inline-flex;margin-top:26px;width:162px;height:40px;border:2px solid #fff;align-items:center;justify-content:center;font-size:18px;color:#fff}
.video{flex:1;background:linear-gradient(135deg,#3e8cc9,#6aa8d8 50%,#4f93cd);color:#fff;text-align:center;padding-top:116px;font-size:18px}
.play{width:56px;height:40px;margin:26px auto 0;background:#fff;border-radius:7px;display:flex;align-items:center;justify-content:center}
.video h3{font-size:18px;font-weight:700;margin-top:16px;letter-spacing:.3px}

/* expertise */
.expertise{height:653px;text-align:center;padding-top:48px}
.center-title{display:inline-block}
.center-title .underline{margin:8px auto 0;width:110px}
.card-grid{display:grid;grid-template-columns:repeat(4,252px);gap:13px 11px;justify-content:center;margin-top:38px}
.card{height:217px;background:linear-gradient(135deg,#e0e0e0 0%,#e0e0e0 50%,#ebebeb 50%,#e8e8e8 100%);position:relative;padding-top:22px}
.card svg.icon{width:56px;height:56px}
.card h3{font-size:15.5px;font-weight:700;color:var(--ink);margin-top:14px}
.card p{font-size:13.5px;line-height:19px;color:var(--ink);margin:10px auto 0;width:200px}
.card .corner{position:absolute;right:0;bottom:0;width:34px;height:34px;background:linear-gradient(135deg,transparent 50%,var(--gold) 50%)}
.card .corner::after{content:"+";position:absolute;right:5px;bottom:1px;color:#fff;font-size:12px;font-weight:700}

/* radio */
.radio{height:297px;background:var(--band);text-align:center;padding-top:42px;position:relative}
.quote{width:960px;margin:34px auto 0;font-style:italic;font-size:14px;line-height:23px;color:var(--ink);position:relative}
.quote .mark{color:var(--gold-soft);font-size:36px;font-style:normal;font-weight:900;position:absolute;left:160px;top:-10px}
.quote-author{color:var(--gold);font-weight:700;font-size:17px;margin-top:14px}
.radio-arrow{position:absolute;top:138px}
.radio-arrow.left{left:74px}.radio-arrow.right{right:74px}

/* footer */
.site-footer{height:174px;position:relative;background:linear-gradient(135deg,#3a3a3a,#2c2c2c 50%,#353535)}
.donate{position:absolute;top:20px;left:0;right:0;display:flex;justify-content:center;align-items:center;gap:10px;color:#fff;font-weight:700;font-size:17px}
.donate .label{margin-right:16px}
.badge{width:91px;height:42px;background:#fff;border-radius:2px}
.footer-contact{position:absolute;top:102px;left:190px;right:110px;display:flex;justify-content:space-between;color:#fff;font-size:14px}
.footer-contact span{display:flex;align-items:center;gap:12px}
.copyright{height:36px;background:var(--blue);color:#fff;font-size:12.5px;display:flex;align-items:center;justify-content:center}
</style>
</head>
<body>

<header class="site-header">
  <div class="brand">Dr. Mara L. Kalvoric</div>
  <div class="contact-pills">
    <div class="pill"><svg viewBox="0 0 20 20"><rect x="2" y="4" width="16" height="12" fill="none" stroke="#c9ad5a" stroke-width="1.6"/><path d="M2 4l8 7 8-7" fill="none" stroke="#c9ad5a" stroke-width="1.6"/></svg>Email Us <b>mk@drkalvoric.com</b></div>
    <div class="pill"><svg viewBox="0 0 20 20"><path d="M5 2l3 4-2 2c1 2.5 3 4.5 6 6l2-2 4 3-2 3C9 18 2 11 2 5z" fill="none" stroke="#c9ad5a" stroke-width="1.5"/></svg>Call Us <b>(555) 310 4826</b></div>
  </div>
</header>

<nav class="main-nav">
  <a class="active">HOME</a><a>BIO</a><a>MY EXPERTISE</a><a>SESSIONS</a><a>RESOURCES</a><a>CONTACT ME</a>
</nav>

<section class="hero" role="img" aria-label="Photo of a counseling session: a client seated on a sofa listening to a therapist">
  <div class="hero-arrow left"><svg width="12" height="14" viewBox="0 0 12 14"><path d="M9 1L3 7l6 6" fill="none" stroke="#fff" stroke-width="2.4"/></svg></div>
  <div class="hero-arrow right"><svg width="12" height="14" viewBox="0 0 12 14"><path d="M3 1l6 6-6 6" fill="none" stroke="#fff" stroke-width="2.4"/></svg></div>
  <div class="hero-caption">I Provide individual and marital counseling</div>
</section>

<section class="about">
  <div class="about-body">
    <h2 class="section-title script">About <span class="accent">Dr. Mara L. Kalvoric</span></h2>
    <div class="underline"></div>
    <p>While I acknowledge the importance of my education, I also appreciate the role my experiences have played in allowing me to relate so well to others. Allow me to share those I feel are most relevant with you.I survived an abusive childhood that my mother and sister unfortunately did not &nbsp;…… <b>Read More</b></p>
    <div class="values">
      <div class="value">
        <div class="value-icon"><svg width="40" height="40" viewBox="0 0 40 40"><path d="M10 36V26c-4-3-5-8-3-13 3-6 12-8 18-4 4 3 5 7 4 11l3 4-3 1v4c0 2-2 3-4 3h-3v4z" fill="#c9ad5a"/><circle cx="19" cy="17" r="4" fill="#fff"/></svg></div>
        <div><h3>My Philosophy</h3><p>Lorem ipsum dolor sit amet,conse ctetuer adipiscing elit,</p></div>
      </div>
      <div class="value">
        <div class="value-icon"><svg width="40" height="40" viewBox="0 0 40 40"><circle cx="20" cy="20" r="14" fill="none" stroke="#c9ad5a" stroke-width="3"/><circle cx="20" cy="20" r="8" fill="none" stroke="#2a84c4" stroke-width="3"/><circle cx="20" cy="20" r="3" fill="#c9ad5a"/><path d="M20 20L33 7" stroke="#2a84c4" stroke-width="2.5"/></svg></div>
        <div><h3>My Mission</h3><p>Lorem ipsum dolor sit amet,conse ctetuer adipiscing elit,</p></div>
      </div>
    </div>
  </div>

  <aside class="inquiry">
    <h2>QUICK INQUIRY</h2>
    <form>
      <div class="field">Full Name</div>
      <div class="field">Phone Number</div>
      <div class="field select">Email</div>
      <div class="field area">Message</div>
      <div class="submit">SUBMIT</div>
    </form>
  </aside>
</section>

<section class="feature-band">
  <div class="sessions">
    <svg width="58" height="58" viewBox="0 0 58 58"><circle cx="23" cy="12" r="9" fill="#fff"/><path d="M6 56V36c0-8 6-13 14-13h8l10 12 14-16 3 3-16 21H30l-2-4v17z" fill="#fff"/></svg>
    <h2>Type of Sessions i Provide</h2>
    <ul class="session-list">
      <li class="strong"><svg width="12" height="10" viewBox="0 0 12 10"><path d="M1 5l3.5 3.5L11 1" fill="none" stroke="#2b2b2b" stroke-width="1.8"/></svg>Individual Sessions</li>
      <li><svg width="12" height="10" viewBox="0 0 12 10"><path d="M1 5l3.5 3.5L11 1" fill="none" stroke="#2b2b2b" stroke-width="1.8"/></svg>Divorce Mediation</li>
      <li><svg width="12" height="10" viewBox="0 0 12 10"><path d="M1 5l3.5 3.5L11 1" fill="none" stroke="#2b2b2b" stroke-width="1.8"/></svg>Marriage Sessions</li>
      <li><svg width="12" height="10" viewBox="0 0 12 10"><path d="M1 5l3.5 3.5L11 1" fill="none" stroke="#2b2b2b" stroke-width="1.8"/></svg>Custody Evaluation Sessions</li>
      <li><svg width="12" height="10" viewBox="0 0 12 10"><path d="M1 5l3.5 3.5L11 1" fill="none" stroke="#2b2b2b" stroke-width="1.8"/></svg>Family Sessions</li>
      <li><svg width="12" height="10" viewBox="0 0 12 10"><path d="M1 5l3.5 3.5L11 1" fill="none" stroke="#2b2b2b" stroke-width="1.8"/></svg>Testing Sessions</li>
      <li><svg width="12" height="10" viewBox="0 0 12 10"><path d="M1 5l3.5 3.5L11 1" fill="none" stroke="#2b2b2b" stroke-width="1.8"/></svg>Phone Sessions</li>
      <li><svg width="12" height="10" viewBox="0 0 12 10"><path d="M1 5l3.5 3.5L11 1" fill="none" stroke="#2b2b2b" stroke-width="1.8"/></svg>Weekend / Holiday Sessions</li>
    </ul>
    <div class="btn-outline">Get Started</div>
  </div>
  <div class="video" role="img" aria-label="Video still of a distressed client in a counseling session, tinted blue">
    <p>Lorem ipsum dolor sit amet, consectetu</p>
    <div class="play"><svg width="16" height="18" viewBox="0 0 16 18"><path d="M2 1l13 8-13 8z" fill="#2a84c4"/></svg></div>
    <h3>WATCH VIDEO</h3>
  </div>
</section>

<section class="expertise">
  <div class="center-title">
    <h2 class="section-title script">My <span class="accent">Expertise</span></h2>
    <div class="underline"></div>
  </div>
  <div class="card-grid">
    <div class="card"><svg class="icon" viewBox="0 0 56 56"><path d="M28 50C10 36 4 28 4 18 4 10 10 5 17 5c5 0 9 3 11 7 2-4 6-7 11-7 7 0 13 5 13 13 0 10-6 18-24 32z" fill="#2b2b2b"/><path d="M28 14l-4 10 8 4-5 12" fill="none" stroke="#e4e4e4" stroke-width="2.5"/></svg><h3>DATING</h3><p>Lorem ipsum dolor sit amet, consectetuer adipiscing elit, sed diam nonummy nibh</p><span class="corner"></span></div>
    <div class="card"><svg class="icon" viewBox="0 0 56 56"><circle cx="19" cy="9" r="5" fill="#2b2b2b"/><circle cx="37" cy="9" r="5" fill="#2b2b2b"/><path d="M13 17h12l3 18h-5v16h-8V35H10z" fill="#2b2b2b"/><path d="M32 17h10v34h-3V34h-4v17h-3z" fill="#2b2b2b"/></svg><h3>MARRIAGE</h3><p>Lorem ipsum dolor sit amet, consectetuer adipiscing elit, sed diam nonummy nibh</p><span class="corner"></span></div>
    <div class="card"><svg class="icon" viewBox="0 0 56 56"><rect x="20" y="6" width="32" height="26" fill="none" stroke="#2b2b2b" stroke-width="3"/><circle cx="11" cy="14" r="5" fill="#2b2b2b"/><path d="M5 22h12l9 6-2 3-7-3v24h-5V38h-2v14H5z" fill="#2b2b2b"/><path d="M36 32v10M30 48l6-6 6 6" stroke="#2b2b2b" stroke-width="3" fill="none"/></svg><h3>PARENTING &amp; PROFESSIONAL</h3><p>Lorem ipsum dolor sit amet, consectetuer adipiscing elit, sed diam nonummy nibh</p><span class="corner"></span></div>
    <div class="card"><svg class="icon" viewBox="0 0 56 56"><circle cx="17" cy="11" r="7" fill="#2b2b2b"/><circle cx="39" cy="11" r="7" fill="#2b2b2b"/><path d="M3 48c0-14 6-22 14-22s14 8 14 22z" fill="#2b2b2b"/><path d="M25 48c0-14 6-22 14-22s14 8 14 22z" fill="#2b2b2b"/><path d="M12 38h10l-3-3M44 42H34l3 3" stroke="#e4e4e4" stroke-width="2.5" fill="none"/></svg><h3>RELATIONSHIPS</h3><p>Lorem ipsum dolor sit amet, consectetuer adipiscing elit, sed diam nonummy nibh</p><span class="corner"></span></div>
    <div class="card"><svg class="icon" viewBox="0 0 56 56"><circle cx="30" cy="10" r="6" fill="#2b2b2b"/><path d="M24 20l-8 14 6 3-6 14h5l8-16-5-3 6-10 6 6 5-3-9-8z" fill="#2b2b2b"/></svg><h3>DEPRESSION &amp; ANXIETY ISSUES</h3><p>Lorem ipsum dolor sit amet, consectetuer adipiscing elit, sed diam nonummy nibh</p><span class="corner"></span></div>
    <div class="card"><svg class="icon" viewBox="0 0 56 56"><path d="M4 12c8-4 16-4 24 0 0 14-4 24-12 24S4 26 4 12z" fill="#2b2b2b"/><path d="M28 16c8-4 16-4 24 0 0 14-4 24-12 24S28 30 28 16z" fill="#2b2b2b"/><circle cx="11" cy="18" r="2.5" fill="#e4e4e4"/><circle cx="21" cy="18" r="2.5" fill="#e4e4e4"/><path d="M11 27q5 4 10 0" stroke="#e4e4e4" stroke-width="2" fill="none"/><circle cx="35" cy="22" r="2.5" fill="#e4e4e4"/><circle cx="45" cy="22" r="2.5" fill="#e4e4e4"/><path d="M35 33q5-4 10 0" stroke="#e4e4e4" stroke-width="2" fill="none"/></svg><h3>PERSONALITY DISORDERS</h3><p>Lorem ipsum dolor sit amet, consectetuer adipiscing elit, sed diam nonummy nibh</p><span class="corner"></span></div>
    <div class="card"><svg class="icon" viewBox="0 0 56 56"><path d="M28 4v44M10 12h36M18 50h20" stroke="#2b2b2b" stroke-width="3"/><path d="M10 12L4 28h12zM46 12l-6 16h12z" fill="none" stroke="#2b2b2b" stroke-width="2"/><path d="M4 28q6 6 12 0M40 28q6 6 12 0" fill="#2b2b2b"/></svg><h3>DIVORCE MEDIATION</h3><p>Lorem ipsum dolor sit amet, consectetuer adipiscing elit, sed diam nonummy nibh</p><span class="corner"></span></div>
    <div class="card"><svg class="icon" viewBox="0 0 56 56"><circle cx="28" cy="22" r="6" fill="#2b2b2b"/><path d="M16 52V38c0-6 5-10 12-10s12 4 12 10v14z" fill="#2b2b2b"/><circle cx="12" cy="14" r="3" fill="#2b2b2b"/><circle cx="20" cy="6" r="3" fill="#2b2b2b"/><circle cx="36" cy="6" r="3" fill="#2b2b2b"/><circle cx="44" cy="14" r="3" fill="#2b2b2b"/></svg><h3>LIFE MANAGEMENT</h3><p>Lorem ipsum dolor sit amet, consectetuer adipiscing elit, sed diam nonummy nibh</p><span class="corner"></span></div>
  </div>
</section>

<section class="radio">
  <div class="center-title">
    <h2 class="section-title script">Radio <span class="accent">Conversations</span></h2>
    <div class="underline"></div>
  </div>
  <svg class="radio-arrow left" width="14" height="26" viewBox="0 0 14 26"><path d="M12 2L2 13l10 11" fill="none" stroke="#999" stroke-width="2"/></svg>
  <svg class="radio-arrow right" width="14" height="26" viewBox="0 0 14 26"><path d="M2 2l10 11L2 24" fill="none" stroke="#999" stroke-width="2"/></svg>
  <blockquote class="quote">
    <span class="mark">“</span>
    Lorem ipsum dolor sit amet, consectetuer adipiscing elit, sed diam nonummy nibh euismod tincidunt ut laoreet dolore magna aliquam erat volutpat. Ut wisi enim ad minim veniam, quis nostrud exerci tation ullamcorper suscipit lobortis nisl ut aliquip ex ea commodo consequat. Duis autem vel eum iriure.
  </blockquote>
  <div class="quote-author">Neil Garrow</div>
</section>

<footer class="site-footer" role="img" aria-label="Dark street map of the office neighborhood">
  <div class="donate"><span class="label">A portion of all revenue is donated to</span><span class="badge"></span><span class="badge"></span></div>
  <div class="footer-contact">
    <span><svg width="16" height="22" viewBox="0 0 16 22"><path d="M8 0C3.6 0 0 3.5 0 8c0 6 8 14 8 14s8-8 8-14c0-4.5-3.6-8-8-8z" fill="#fff"/><circle cx="8" cy="8" r="3" fill="#333"/></svg>418 Linden Court, Suite 120 Harbor Vale, CA 90210</span>
    <span><svg width="14" height="20" viewBox="0 0 14 20"><path d="M3 1l3 4-2 2c.5 3 2 5 4 6l2-2 3 3-2 4C5 17 0 10 1 3z" fill="#fff"/></svg>(555) 310 4826</span>
    <span><svg width="22" height="16" viewBox="0 0 22 16"><rect x="1" y="1" width="20" height="14" fill="#fff"/><path d="M1 1l10 8 10-8" fill="none" stroke="#333" stroke-width="1.5"/></svg>mk@drkalvoric.com</span>
  </div>
</footer>
<div class="copyright">Copyright 2016 Dr. Mara L. Kalvoric. All Right Reserved</div>

</body>
</html>
```